Dental Practice Billboard Design

We are a newer dental practice in need of a simple but appealing billboard for our growing dental practice to attract new patients. The practice is owned by husband and wife dentists and is family friendly in a small town in Kentucky. We try to be very friendly and caring to our patients. Would prefer a blue background for the billboard and our tooth logo to be prominent. We are partial to the Patua One font used in the image below but please feel free to tweak it as you deem necessary. The shape of the uppercase D and lowercase g are why we like that font, so fonts with a similarly shaped “D” and “g” would work as well. Please include our phone number (555) 847-1390. Please see our website Harlowbrookdentistry.example for more info on the practice if needed. Thank you! Looking forward to seeing your creation.
Updates

The dimensions will be 12ft x 24ft (3.6576m x 7.3152m). Apologies for not including this in the original prompt. Thank you all for your submissions.

Industry/Entity Type

Dental

Font styles to use
Other font styles liked:
• Patua One

Colors
0054AA
0677BA
7BADD7
CADEEF
E8F1F8
0094D4
00A9DD
6FCCEA
C7EBF8
E9F6FB
00AB8E
00BBA5
67D7C9
C6EFE9
E9F9F6
59FF00
82FF00
B8FF75
E3FFCB
F4FFEA

Requirements
Must have
• Phone number, website, Logo, Practice name “Harlow Brook Dentistry”
Should not have
• A tagline or slogan

```html
<!DOCTYPE html>
<html lang="en">
<head>
<meta charset="UTF-8">
<title>Harlow Brook Dentistry – Billboard</title>
<link rel="stylesheet" href="https://fonts.googleapis.com/css2?family=Patua+One&family=Fira+Sans+Condensed:wght@600&display=swap">
<style>
  :root {
    --navy-deep: #0a2360;
    --navy: #0b2d72;
    --blue: #0054aa;
    --blue-bright: #0677ba;
    --green: #00b40f;
    --white: #ffffff;
    --stage: #e8f1f8;
    --photo-a: #dfe6ee;
    --photo-b: #7badd7;
  }
  * { margin: 0; padding: 0; box-sizing: border-box; }
  html, body {
    width: 1200px; height: 722px; overflow: hidden;
    background: var(--stage);
  }
  .billboard {
    position: absolute; left: 30px; top: 76px;
    width: 1140px; height: 570px; overflow: hidden;
    background: linear-gradient(100deg, var(--navy-deep) 0%, var(--navy) 35%, var(--blue) 75%, var(--blue-bright) 100%);
  }
  .brand {
    position: absolute; left: 20px; top: 40px; width: 460px;
    text-align: center; color: var(--white);
    font-family: "Patua One", serif;
  }
  .brand-dot {
    width: 120px; height: 120px; margin: 0 auto 34px;
    border-radius: 50%; background: var(--green);
  }
  .brand-name { font-size: 78px; line-height: 1; }
  .brand-sub { font-size: 54px; line-height: 1.15; margin-top: 10px; }
  .doctors-photo {
    position: absolute; left: 540px; top: 60px;
    width: 570px; height: 380px;
    background: linear-gradient(180deg, var(--photo-b) 0%, var(--photo-a) 55%, var(--white) 100%);
    opacity: .55; border-radius: 6px;
  }
  .bands { position: absolute; left: 0; top: 0; }
  .phone {
    position: absolute; left: 20px; top: 478px;
    display: flex; align-items: center; gap: 12px;
    font-family: "Fira Sans Condensed", sans-serif; font-weight: 600;
    font-size: 68px; color: var(--navy-deep); line-height: 1;
  }
  .web {
    position: absolute; left: 580px; top: 478px;
    display: flex; align-items: center; gap: 14px;
    font-family: "Patua One", serif; font-size: 34px; color: var(--white);
  }
</style>
</head>
<body>
  <main class="billboard">
    <div class="doctors-photo" role="img" aria-label="Portrait photo of the two smiling dentists in white lab coats"></div>

    <svg class="bands" width="1140" height="570" viewBox="0 0 1140 570" aria-hidden="true">
      <polygon points="0,462 472,440 520,570 0,570" fill="var(--white)"/>
      <polygon points="494,439 1140,420 1140,570 542,570" fill="var(--green)"/>
    </svg>

    <div class="brand">
      <div class="brand-dot"></div>
      <div class="brand-name">Harlow Brook</div>
      <div class="brand-sub">Dentistry</div>
    </div>

    <div class="phone">
      <svg width="58" height="58" viewBox="0 0 58 58" aria-hidden="true">
        <circle cx="29" cy="29" r="29" fill="var(--green)"/>
        <path d="M20 15c2-1 4 0 5 2l2 5c1 2 0 3-1 4l-2 2c1 3 4 6 7 7l2-2c1-1 2-2 4-1l5 2c2 1 3 3 2 5l-1 3c-1 2-3 3-6 2-10-2-18-10-20-20-1-3 0-5 3-7z" fill="var(--white)"/>
      </svg>
      <span>(555) 847-1390</span>
    </div>

    <div class="web">
      <svg width="46" height="38" viewBox="0 0 46 38" aria-hidden="true">
        <rect x="7" y="3" width="32" height="22" rx="2" fill="none" stroke="var(--white)" stroke-width="4"/>
        <rect x="1" y="29" width="44" height="5" rx="2" fill="var(--white)"/>
      </svg>
      <span>Harlowbrookdentistry.example</span>
    </div>
  </main>
</body>
</html>
```